Creation of a construction/bricklaying business website

Following the template format of "Halloway 7", the following content would need to be included:
1. Landing page with 3 tiles that go to their own pages.
- Landing page to include background photo and description of services offered.
2. 3 tiles to include:
a) "Contact Us For A Free Quote or Friendly Discussion" Form (middle tile)
b) Case Studies and Testimonials
c) Certifications and Professional Membership
- Design logo to be used from previous SketchNestle project. Example of logo attached below, please access full JPG files from our account.

Target Market(s)

Prospective clients seeking construction work (bricklaying speciality)

Industry/Entity Type

Residential Construction

Coding

Coded - Design and coding required

Number of Pages Required

4 page

Font styles to use
Sans Serif

Colors

Designer to choose colors to be used in the design.

Requirements
Must have
• Following the template format of "Halloway 7", the following content would need to be included:
• 1. Landing parent page with 3 tiles that go to the 3 child pages.
• - Landing page to include background photo and description of services offered.
• 2. 3 tiles to include:
• a) "Contact Us For A Free Quote or Friendly Discussion" Form (middle tile)
• b) Case Studies and Testimonials (first tile / left side)
• c) Certifications and Professional Memberships (third tile / right side) (This should include logos of the relevant organisations being displayed. Specifically GQT and the Pillar Seal GQT).
• - Design logo to be used from previous SketchNestle project. Example of logo attached below, please access full JPG files from our account.
Nice to have
• Sleek and modern feel.
• Approachable in terms of how people can contact the company for a quote.
• Traditional pictures to give credibility and comfort around choosing this company.
Should not have
• Cheesy pictures
• Over-complicated
• Simple to use
• Easy URL domain name

```html
<!DOCTYPE html>
<html lang="en">
<head>
<meta charset="utf-8">
<title>R.T. Hale Construction Ltd</title>
<link href="https://fonts.googleapis.com/css2?family=Roboto:wght@300;400;500;700&display=swap" rel="stylesheet">
<style>
:root{
  --navy:#1c3f7a;
  --blue:#2a5caa;
  --sky-top:#3d78c4;
  --sky-bottom:#a9c6e6;
  --tile-grey:#eeeff2;
  --tile-white:#f8f8f9;
  --ink:#3a3f47;
  --muted:#7a808a;
  --badge-red:#c9252b;
  --line:#d9dce1;
  --band:#dadcdf;
}
*{box-sizing:border-box;margin:0;padding:0}
html,body{width:694px;height:1200px;overflow:hidden}
body{position:relative;font-family:"Roboto",sans-serif;color:var(--ink);background:#fff}

.hero{position:absolute;left:0;top:0;width:694px;height:560px;
  background:linear-gradient(180deg,var(--sky-top) 0%,#6d9bd3 45%,var(--sky-bottom) 100%)}
.brand{position:absolute;left:34px;top:14px;color:#fff;font-weight:700;font-size:24px;line-height:1;display:flex;align-items:center;gap:8px}
.brand-mark{width:12px;height:12px;background:#fff}
.brand small{display:block;font-size:9px;font-weight:500;letter-spacing:1px;margin-top:3px}
.menu{position:absolute;right:38px;top:22px;width:34px;height:34px;border-radius:50%;background:#fff;display:flex;align-items:center;justify-content:center}
.menu span{width:14px;height:2px;background:var(--navy);box-shadow:0 -4px 0 var(--navy),0 4px 0 var(--navy)}
.menu-label{position:absolute;right:44px;top:60px;color:#fff;font-size:8px;font-weight:700}
.hero-title{position:absolute;left:40px;top:150px;color:var(--navy);font-weight:700;font-size:31px;line-height:1.15}
.btn{display:inline-block;background:var(--navy);color:#fff;font-size:10px;font-weight:700;letter-spacing:.5px;padding:8px 16px}
.hero-btn{position:absolute;left:40px;top:224px}

.tiles{position:absolute;left:0;top:300px;width:694px;height:400px}
.tiles svg{position:absolute;left:0;top:0}
.tile{position:absolute;top:0;height:400px}
.tile-left{left:0;width:208px;padding:60px 26px 0 36px}
.tile-mid{left:208px;width:262px;text-align:center;padding-top:200px}
.tile-right{left:470px;width:224px;text-align:center;padding-top:82px}
.tile h2{font-weight:300;font-size:19px;line-height:1.25;color:var(--ink)}
.rule{width:70px;height:3px;background:var(--blue);margin-top:10px}
.quote{font-size:38px;color:var(--navy);font-weight:700;margin-top:22px;line-height:.8}
.testimonial{font-size:8.5px;line-height:1.5;color:var(--muted);margin-top:8px}
.person{display:flex;align-items:center;gap:8px;margin-top:20px}
.avatar{width:24px;height:24px;border-radius:50%;background:#8a6f5a}
.person b{display:block;font-size:7px;color:var(--ink)}
.person span{font-size:7px;color:var(--muted)}
.view-all{position:absolute;left:152px;top:390px;font-size:7px;padding:5px 9px}
.tile-mid h2{font-size:20px}
.tile-mid .btn{margin-top:26px;padding:9px 20px}
.badge{width:62px;height:42px;background:var(--badge-red);margin:0 auto}
.badge-one{margin-top:40px;background:#fff;border:6px solid var(--badge-red)}
.badge-two{margin-top:24px;height:62px}

.services{position:absolute;left:0;top:715px;width:694px;text-align:center}
.services h2{font-weight:300;font-size:24px;color:var(--ink)}
.services p{font-size:8.5px;color:var(--muted);width:250px;margin:10px auto 0;line-height:1.5}
.services .rule{margin:14px auto 0;width:44px}
.service-row{display:flex;justify-content:center;margin-top:36px}
.service{width:90px;height:80px;border-left:1px solid var(--line);display:flex;flex-direction:column;align-items:center;justify-content:flex-start;padding-top:6px}
.service:first-child{border-left:none}
.service svg{width:32px;height:32px}
.service span{font-size:8.5px;font-weight:500;color:var(--ink);margin-top:6px;line-height:1.2}

.about{position:absolute;left:0;top:1000px;width:694px;height:145px;
  background:linear-gradient(180deg,#e2e3e5,var(--band));text-align:center;padding-top:30px}
.about p{font-size:9px;line-height:1.45;color:var(--muted);width:380px;margin:0 auto}
.about p.cta{color:var(--ink);font-weight:500;margin-top:10px;width:260px}

.footer{position:absolute;left:0;top:1145px;width:694px;height:55px;background:var(--navy)}
.footer .brand{left:30px;top:14px;font-size:20px}
.footer .legal{position:absolute;right:34px;top:22px;color:#c5d0e2;font-size:7px}
</style>
</head>
<body>

<header class="hero" role="img" aria-label="Photo of a high-rise building under construction with tower cranes against a blue sky">
  <div class="brand"><span class="brand-mark"></span><div>R.T. Hale<small>CONSTRUCTION LTD</small></div></div>
  <div class="menu"><span></span></div>
  <div class="menu-label">MENU</div>
  <h1 class="hero-title">Construction &amp;<br>Brick laying</h1>
  <a class="btn hero-btn">Read More</a>
</header>

<section class="tiles">
  <svg width="694" height="400" viewBox="0 0 694 400" aria-hidden="true">
    <polygon points="0,30 208,10 208,400 0,400" fill="#eeeff2" opacity=".96"/>
    <polygon points="208,10 339,70 470,10 470,400 208,400" fill="#f8f8f9"/>
    <polygon points="470,10 694,30 694,400 470,400" fill="#eeeff2" opacity=".96"/>
  </svg>

  <article class="tile tile-left">
    <h2>Case Studies<br>and Testimonials</h2>
    <div class="rule"></div>
    <div class="quote">&ldquo;</div>
    <p class="testimonial">We hired the team for an extension and the work was tidy, on time and on budget. The bricklayers were friendly and kept us informed at every stage.</p>
    <div class="person"><div class="avatar"></div><div><b>DANIEL MORETON</b><span>England</span></div></div>
  </article>
  <a class="btn view-all">VIEW ALL</a>

  <article class="tile tile-mid">
    <h2>Contact Us For<br>A Free Quote or<br>Friendly Discussion</h2>
    <a class="btn">GET A QUOTE</a>
  </article>

  <article class="tile tile-right">
    <h2>Certifications<br>and Professional<br>Memberships</h2>
    <div class="badge badge-one"></div>
    <div class="badge badge-two"></div>
  </article>
</section>

<section class="services">
  <h2>Our Services</h2>
  <p>R.T. Hale Construction Ltd is a construction company that has expertise and experience in the following areas:</p>
  <div class="rule"></div>
  <div class="service-row">
    <div class="service">
      <svg viewBox="0 0 32 32" fill="none" stroke="#2a5caa" stroke-width="1.6"><rect x="4" y="12" width="14" height="16"/><rect x="18" y="18" width="10" height="10"/><path d="M2 13 11 5 20 13"/><rect x="8" y="18" width="5" height="5"/></svg>
      <span>Extensions</span>
    </div>
    <div class="service">
      <svg viewBox="0 0 32 32" fill="none" stroke="#2a5caa" stroke-width="1.6"><path d="M4 15 16 5 28 15"/><rect x="7" y="14" width="18" height="14"/><rect x="14" y="20" width="4" height="8"/></svg>
      <span>New build /<br>New houses</span>
    </div>
    <div class="service">
      <svg viewBox="0 0 32 32" fill="none" stroke="#2a5caa" stroke-width="1.6"><rect x="3" y="8" width="26" height="18"/><path d="M3 14h26M3 20h26M10 8v6M22 8v6M16 14v6M10 20v6M22 20v6"/></svg>
      <span>Garden walls</span>
    </div>
    <div class="service">
      <svg viewBox="0 0 32 32" fill="none" stroke="#2a5caa" stroke-width="1.6"><path d="M6 12 20 6 26 12 12 18Z"/><path d="M16 15v6M13 21h6v7h-6z"/></svg>
      <span>Plastering</span>
    </div>
    <div class="service">
      <svg viewBox="0 0 32 32" fill="none" stroke="#2a5caa" stroke-width="1.6"><rect x="5" y="12" width="22" height="14"/><path d="M5 19h22M12 12v7M20 19v7"/><path d="M9 12V7h14v5"/></svg>
      <span>Brickwork</span>
    </div>
    <div class="service">
      <svg viewBox="0 0 32 32" fill="none" stroke="#2a5caa" stroke-width="1.6"><path d="M2 24h28"/><path d="M4 20h14l3-5h6v5"/><circle cx="8" cy="22" r="2"/><circle cx="22" cy="22" r="2"/><path d="M21 15 26 8"/></svg>
      <span>Groundworks</span>
    </div>
  </div>
</section>

<section class="about" role="img" aria-label="Faint background photo of a finished brick building">
  <p>We pride ourselves on attention to detail, pride in our completed project and client satisfaction. We believe in full transparency and this is reflected in the price we quote for you. We break down each step with both labour and materials cost so you can see exactly what you are paying for.</p>
  <p class="cta">Feel free to get in touch and we can talk through what you are looking to achieve.</p>
</section>

<footer class="footer">
  <div class="brand"><span class="brand-mark"></span><div>R.T. Hale<small>CONSTRUCTION LTD</small></div></div>
  <div class="legal">Copyright © 2018 All Rights Reserved</div>
</footer>

</body>
</html>
```